Business card design for Virtual Assistance company

I need a business card designed for my virtual assistance company. We are a small company who services primarily C-level executive clients. The card needs to be double sided with the following contact information on the back:
Melissa Thornbury
Owner/CEO
info@rkpadvisory.net
www.rkpadvisory.net
555.302.9817

The front side should just have the company name incorporated: "RKP Advisory" and "virtual assistance"

The card should be simplistic, but eye catching and should speak to high level executives. Our primary focus areas consist of executive assistance and government contracting.

Target Market(s)

CEOs and executives

Contact Information for Business Card

see project description. phone, email, website.

Colors

Designer to choose only greyscale colors for use in the design.

```html
<!DOCTYPE html>
<html lang="en">
<head>
<meta charset="utf-8">
<title>RKP Advisory – Business Card</title>
<link rel="stylesheet" href="https://fonts.googleapis.com/css2?family=Crimson+Text:wght@400;600;700&family=Montserrat:wght@400;500&display=swap">
<style>
  :root {
    --backdrop: #d6d4d0;
    --card: #1c1c1c;
    --card-edge: #141414;
    --ink-light: #f4f4f4;
    --ink-soft: #dcdcdc;
    --mark-tone: #262626;
    --mark-deep: #111111;
  }
  * { margin: 0; padding: 0; box-sizing: border-box; }
  html, body {
    width: 900px; height: 1200px; overflow: hidden;
    background: var(--backdrop);
  }
  .canvas { position: relative; width: 900px; height: 1200px; }
  .card {
    position: absolute; left: 80px; width: 742px; height: 441px;
    background: var(--card);
    border-radius: 24px;
    box-shadow: 0 6px 18px rgba(0,0,0,0.35);
    overflow: hidden;
  }
  .card--front { top: 131px; }
  .card--back { top: 638px; }

  .company-name {
    position: absolute; left: 30px; top: 30px;
    font-family: "Crimson Text", serif; font-weight: 600;
    font-size: 50px; line-height: 1; color: var(--ink-light);
  }
  .person { position: absolute; left: 42px; top: 198px; }
  .person__name {
    font-family: "Crimson Text", serif; font-weight: 700;
    font-size: 27px; line-height: 1; color: var(--ink-light);
  }
  .person__role {
    margin-top: 6px;
    font-family: "Montserrat", sans-serif; font-size: 16px; color: var(--ink-soft);
  }
  .contacts { position: absolute; left: 42px; top: 289px; list-style: none; }
  .contacts__item {
    display: flex; align-items: center; height: 28px;
    font-family: "Montserrat", sans-serif; font-size: 16px; color: var(--ink-soft);
  }
  .contacts__icon { width: 18px; height: 18px; margin-right: 8px; fill: var(--ink-soft); }
  .tagline {
    position: absolute; left: 42px; top: 390px;
    font-family: "Crimson Text", serif; font-size: 17px;
    letter-spacing: 0.3px; color: var(--ink-soft);
  }
  .front-accent {
    position: absolute; left: 360px; top: 110px; width: 300px; height: 300px;
    border-radius: 50%;
    background: radial-gradient(circle at 35% 30%, var(--mark-tone), var(--mark-deep));
  }
  .back-name {
    position: absolute; inset: 0;
    display: flex; align-items: center; justify-content: center;
    font-family: "Crimson Text", serif; font-weight: 600;
    font-size: 96px; color: var(--mark-deep);
  }
</style>
</head>
<body>
<main class="canvas">
  <section class="card card--front" aria-label="Card front">
    <div class="front-accent"></div>
    <h1 class="company-name">RKP Advisory</h1>
    <div class="person">
      <p class="person__name">Melissa Thornbury</p>
      <p class="person__role">Owner/CEO</p>
    </div>
    <ul class="contacts">
      <li class="contacts__item">
        <svg class="contacts__icon" viewBox="0 0 24 24" aria-hidden="true"><path d="M6.6 10.8a15.1 15.1 0 0 0 6.6 6.6l2.2-2.2a1 1 0 0 1 1-.25 11.4 11.4 0 0 0 3.6.57 1 1 0 0 1 1 1V20a1 1 0 0 1-1 1A17 17 0 0 1 3 4a1 1 0 0 1 1-1h3.5a1 1 0 0 1 1 1c0 1.25.2 2.45.57 3.57a1 1 0 0 1-.25 1z"/></svg>
        555.302.9817
      </li>
      <li class="contacts__item">
        <svg class="contacts__icon" viewBox="0 0 24 24" aria-hidden="true"><path d="M3 6h18v12H3z M3 6l9 7 9-7" fill="none" stroke="#dcdcdc" stroke-width="0"/><path d="M3 7.2 12 13l9-5.8V18H3z M3.5 6h17L12 11.5z"/></svg>
        info@rkpadvisory.net
      </li>
      <li class="contacts__item">
        <svg class="contacts__icon" viewBox="0 0 24 24" aria-hidden="true"><circle cx="12" cy="12" r="9" fill="none" stroke="#dcdcdc" stroke-width="2"/><path d="M3 12h18M12 3c3 3 3 15 0 18M12 3c-3 3-3 15 0 18" fill="none" stroke="#dcdcdc" stroke-width="1.6"/></svg>
        www.rkpadvisory.net
      </li>
    </ul>
    <p class="tagline">VIRTUAL ASSISTANCE</p>
  </section>

  <section class="card card--back" aria-label="Card back">
    <p class="back-name">RKP Advisory</p>
  </section>
</main>
</body>
</html>
```